Electrical & Communications Company Wordpress Themed Website Design

Hi everyone,

I need a wordpress themed website designed for a new company based in Sydney Australia called "VELTRIX". It delivers electrical and communication services to the domestic and commercial sectors.

It needs to be the FULL/COMPLETE wordpress theme! A clean and easy to use site.

Please guys take the time to look at these competitors sites:

www.quillspark.com.au
www.marbleforgeelectrical.com.au
www.tzo.com.au
www.lanternvolt.com.au
www.brockleyelectrical.com.au
www.zephelectricians.com.au

Please use these site for ideas only!!! we want to be original.

(If you would like to add electrical and communications to the logo that is O.K.)

Note: These logo's are registered trademarks of veltrix pty ltd.

Accreditation:

Wupa member (Federated wiring and signalling guild)

PLEASE CHECK THE WEB PLANNING LAYOUT BELOW FOR ROUGH IDEA
Updates

Have requested to increase payment to $400 and now guarantee payment!

Hi guys, forgot to mention i would like to see the business phone number prominently some where with a call to action.As we are a service business and need people to easly be able to see our contact number. Maybe top right courner but open to ideas. 

 Guys/Girls this is for a complete working word press theme that i can load up on the sever and access thru wordpress admin. Code etc

Industry/Entity Type

Communications

Requirements
Must have
• - Logo Provided must be used
• - Themes and colours to be consisted with with brand
• - Fully customizable
• - Have a social share button from sharevio.com
• - Must be the full/complete theme for word press
Nice to have
• - pixmerrows
• - contactform
• - would like kora trovo card zelbin displayed
• - Guarantee logo or something
Should not have
• - Please don't waste your or our time submitting templates or copies of other sites original only!

```html
<!DOCTYPE html>
<html lang="en">
<head>
<meta charset="utf-8">
<title>VELTRIX – Electrical &amp; Communications</title>
<link href="https://fonts.googleapis.com/css2?family=Open+Sans:wght@400;600;700&family=Arimo:wght@400;700&display=swap" rel="stylesheet">
<style>
:root{
  --red:#e0161d;
  --red-dark:#b80d12;
  --red-light:#f23a3f;
  --ink:#222;
  --text:#555;
  --grey-band:#ececec;
  --grey-line:#c9c9c9;
  --field:#fff;
  --black:#111;
  --gold:#e0b21f;
  --sky:#4a6390;
}
*{box-sizing:border-box;margin:0;padding:0}
html,body{width:1013px;height:1200px;overflow:hidden;background:#fff}
body{position:relative;font-family:"Open Sans",Verdana,sans-serif;color:var(--text)}
.abs{position:absolute}

/* header */
.site-header{left:0;top:0;width:1013px;height:71px;background:var(--grey-band);border-bottom:1px solid var(--grey-line)}
.brand{left:130px;top:14px;display:flex;align-items:center;gap:8px;font-family:"Arimo",Arial,sans-serif;font-weight:700;font-size:34px;color:var(--red);letter-spacing:1px}
.brand-dot{width:22px;height:22px;border-radius:50%;background:var(--red)}
.call-now{right:121px;top:22px;font-family:"Arimo",Arial,sans-serif;color:var(--ink);font-size:15px;white-space:nowrap}
.call-now strong{color:var(--red);font-size:27px;font-weight:700;margin-left:6px;font-family:Georgia,serif}

.share{right:121px;top:79px;display:flex;align-items:center;gap:5px;font-size:10px;color:#2a5db0;font-weight:600}
.share-box{width:12px;height:12px;background:#f26b1d}

/* nav */
.main-nav{left:121px;top:100px;width:771px;height:31px;background:linear-gradient(var(--red-light),var(--red));display:flex;border-radius:4px 4px 0 0}
.main-nav a{color:#fff;font-family:"Arimo",Arial,sans-serif;font-weight:700;font-size:14px;text-decoration:none;padding:7px 22px 0;border-right:1px solid var(--red-dark);height:31px;white-space:nowrap}

/* hero */
.hero-photo{left:121px;top:131px;width:534px;height:289px;background:linear-gradient(160deg,#8aa4d0 0%,var(--sky) 40%,#23304d 100%)}
.promo{left:655px;width:237px;height:96px;display:flex;flex-direction:column;justify-content:center;align-items:flex-end;padding-right:14px;font-family:"Arimo",Arial,sans-serif;font-weight:700;white-space:nowrap}
.promo-247{top:131px;background:linear-gradient(#eaeaea,#bdbdbd)}
.promo-247 .big{color:var(--red);font-size:29px}
.promo-247 .small{color:#333;font-size:18px}
.promo-callout{top:228px;background:linear-gradient(var(--red-light),var(--red-dark))}
.promo-callout .big{color:#fff;font-size:23px}
.promo-fixed{top:325px;height:95px;background:linear-gradient(120deg,#333 0%,#333 22%,#cfc7bb 23%,#eee 100%);align-items:flex-start;padding-left:10px}
.promo-fixed .small{color:#fff;font-size:11px;transform:rotate(-45deg);margin-top:30px}

/* content */
.main{left:121px;top:445px;width:480px}
.section-title{font-family:"Arimo",Arial,sans-serif;color:var(--red);font-size:20px;font-weight:400;margin-bottom:2px}
.main p{font-size:10.8px;line-height:14.5px;margin-bottom:14.5px}
.testimonials{left:121px;top:897px;width:480px}
.testimonials .section-title{font-size:16px;margin-bottom:6px}
.quote{position:relative;padding:0 4px 0 22px;font-size:10.8px;line-height:14.5px}
.quote-mark{position:absolute;font-family:Georgia,serif;font-size:40px;color:#c8c8c8;line-height:1}
.qm-open{left:0;top:-6px}
.qm-close{right:0;top:44px}
.quote cite{display:block;font-style:normal;font-size:9.5px;font-weight:700;color:var(--ink);margin-top:6px;line-height:12px}

/* sidebar */
.widget{left:680px;width:212px;border:2px solid var(--red);border-radius:7px}
.contact-widget{top:457px;height:246px;background:linear-gradient(var(--red-light),var(--red-dark));padding:8px 12px}
.widget-title{font-family:"Arimo",Arial,sans-serif;color:#fff;font-weight:700;font-size:19px;display:flex;align-items:center;gap:10px}
.icon-note{width:28px;height:28px;background:#fff;border-radius:3px;transform:rotate(-12deg)}
.field{background:var(--field);height:20px;margin-top:6px;font-size:9.5px;color:#aaa;padding:3px 6px}
.field.msg{height:80px}
.form-buttons{display:flex;justify-content:center;gap:8px;margin-top:8px}
.btn{background:linear-gradient(#f4f4f4,#cfcfcf);font-size:10.5px;font-weight:700;color:#555;width:66px;height:22px;text-align:center;line-height:22px}
.search-widget{top:716px;height:47px;background:linear-gradient(var(--red-light),var(--red-dark));padding:11px 12px;display:flex}
.search-widget .field{margin:0;flex:1}
.search-btn{width:30px;height:20px;background:#e7e7e7}
.blog-widget{top:777px;height:170px;background:#fff;overflow:hidden}
.blog-head{height:46px;background:linear-gradient(var(--red-light),var(--red));display:flex;align-items:center;gap:10px;padding-left:10px;font-family:"Arimo",Arial,sans-serif;color:#fff;font-weight:700;font-size:17px;white-space:nowrap}
.rss{width:32px;height:32px;border-radius:5px;background:#f48a1f}
.blog-body{padding:8px 10px;font-size:10.4px;line-height:13px;color:var(--ink)}
.blog-thumb{float:left;width:92px;height:64px;margin-right:8px;background:linear-gradient(135deg,#1b3b7a,#5878b0)}
.blog-body b{font-size:10px}
.read-more{text-align:right;font-weight:700;font-size:10px;margin-top:3px}
.pay-widget{top:960px;height:48px;background:#fff;display:flex;align-items:center;gap:6px;padding:0 8px;font-size:9.5px;font-weight:700;color:var(--ink);white-space:nowrap}
.pay-name{font-size:9.5px;font-weight:700;color:#1a3d8f}
.seal-dot{width:18px;height:18px;border-radius:50%;border:2px solid #333;flex:none}

/* footer */
.site-footer{left:0;top:1027px;width:1013px;height:137px;background:var(--grey-band);border-top:1px solid var(--grey-line)}
.partners{left:121px;top:1027px;width:236px;height:137px;border-right:2px dotted #bbb;text-align:center;padding-top:14px}
.partners h4{font-size:10.5px;color:var(--ink);font-weight:700}
.partner-name{display:inline-flex;align-items:center;gap:8px;margin-top:28px;font-family:"Arimo",Arial,sans-serif;font-weight:700;font-size:28px;color:#1b3d7c}
.partner-sq{width:20px;height:20px;background:#1b3d7c}
.seal{left:427px;top:1042px;width:108px;height:108px;border-radius:50%;background:radial-gradient(#f3cf4a,var(--gold) 70%,#b98a10)}
.footer-divider{left:605px;top:1027px;height:137px;border-left:2px dotted #bbb}
.footer-brand{left:655px;top:1046px;display:flex;align-items:center;gap:6px;font-family:"Arimo",Arial,sans-serif;font-weight:700;font-size:26px;color:var(--ink)}
.footer-brand .brand-dot{width:18px;height:18px;background:var(--ink)}
.address{left:675px;top:1093px;font-size:10.5px;line-height:14.5px;color:var(--ink);font-style:normal}
.bottom-bar{left:0;top:1164px;width:1013px;height:36px;background:var(--black);color:#fff;font-size:10px;font-weight:700;display:flex;justify-content:space-between;align-items:center;padding:0 121px}
</style>
</head>
<body>

<header class="abs site-header"></header>
<div class="abs brand"><span class="brand-dot"></span>VELTRIX</div>
<div class="abs call-now">Call Now <strong>1300 582 614</strong></div>
<div class="abs share"><span class="share-box"></span>Share</div>

<nav class="abs main-nav">
  <a href="#">Home</a><a href="#">About Us</a><a href="#">Products</a><a href="#">Services</a><a href="#">Blog</a><a href="#">Contact Us</a>
</nav>

<div class="abs hero-photo" role="img" aria-label="Photo of a glass office tower overlooking a city skyline at dusk"></div>
<div class="abs promo promo-247" role="img" aria-label="Support operator photo panel"><span class="big">24 X 7</span><span class="small">A WEEK</span></div>
<div class="abs promo promo-callout"><span class="big">No! CALLOUT FEE</span></div>
<div class="abs promo promo-fixed" role="img" aria-label="Photo of an electrician fitting a ceiling light"><span class="small">FIXED PRICING</span></div>

<main class="abs main">
  <h1 class="section-title">Welcome to VELTRIX</h1>
  <p>Lorem Ipsum is simply dummy text of the printing and typesetting industry. Lorem Ipsum has been the industry's standard dummy text ever since the 1500s, when an unknown printer took a galley of type and scrambled it to make a type specimen book.</p>
  <p>It has survived not only five centuries, but also the leap into electronic typesetting, remaining essentially unchanged. It was popularised in the 1960s with the release of Typeveil sheets containing Lorem Ipsum passages, and more recently with desktop publishing software like Folio Layoutmaker including versions of Lorem Ipsum.</p>
  <p>It is a long established fact that a reader will be distracted by the readable content of a page when looking at its layout. The point of using Lorem Ipsum is that it has a more-or-less normal distribution of letters, as opposed to using 'Content here, content here', making it look like readable English.</p>
  <p>Many desktop publishing packages and web page editors now use Lorem Ipsum as their default model text, and a search for 'lorem ipsum' will uncover many web sites still in their infancy. Various versions have evolved over the years, sometimes by accident, sometimes on purpose (injected humour and the like).</p>
  <p>It is a long established fact that a reader will be distracted by the readable content of a page when looking at its layout. The point of using Lorem Ipsum is that it has a more-or-less normal distribution of letters, as opposed to using 'Content here, content here', making it look like readable English.</p>
  <p>Many desktop publishing packages and web page editors now use Lorem Ipsum as their default model text, and a search for 'lorem ipsum' will uncover many web sites still in their infancy. Various versions have evolved over the years, sometimes by accident, sometimes on purpose (injected humour and the like).</p>
</main>

<section class="abs testimonials">
  <h2 class="section-title">Testimonials</h2>
  <blockquote class="quote">
    <span class="quote-mark qm-open">&ldquo;</span>
    Lorem Ipsum is simply dummy text of the printing and typesetting industry. Lorem Ipsum has been the industry's standard dummy text ever since the 1500s, when an unknown printer took a galley of type and scrambled it to make a type specimen book.
    <cite>Delia<br>Executive</cite>
    <span class="quote-mark qm-close">&rdquo;</span>
  </blockquote>
</section>

<aside>
  <div class="abs widget contact-widget">
    <div class="widget-title"><span class="icon-note"></span>Contact Us</div>
    <div class="field">Name</div>
    <div class="field">Email</div>
    <div class="field">Subject</div>
    <div class="field msg">Message</div>
    <div class="form-buttons"><span class="btn">Submit</span><span class="btn">Clear</span></div>
  </div>
  <div class="abs widget search-widget">
    <div class="field">Search..</div>
    <span class="search-btn">
      <svg width="30" height="20" viewBox="0 0 30 20"><circle cx="14" cy="9" r="5" fill="none" stroke="#888" stroke-width="2"/><line x1="18" y1="13" x2="22" y2="17" stroke="#888" stroke-width="2"/></svg>
    </span>
  </div>
  <div class="abs widget blog-widget">
    <div class="blog-head"><span class="rss"></span>Recent Blog Post</div>
    <div class="blog-body">
      <div class="blog-thumb" role="img" aria-label="Blog thumbnail about fair pricing"></div>
      <b>Topic By<br>R.T. Marlow</b><br>01-05-2010<br>Lorem Ipsum is simply dummy text of the printing and typesetting industry.
      <div class="read-more">Read More</div>
    </div>
  </div>
  <div class="abs widget pay-widget">
    <span>Pay With:</span>
    <span class="pay-name">trovo card</span>
    <span class="pay-name">kora</span>
    <span class="pay-name">Amaro</span>
    <span class="seal-dot"></span>
  </div>
</aside>

<footer>
  <div class="abs site-footer"></div>
  <div class="abs partners">
    <h4>OUR PARTNERS</h4>
    <div class="partner-name"><span class="partner-sq"></span>Wupa</div>
  </div>
  <div class="abs seal" role="img" aria-label="Satisfaction guarantee seal"></div>
  <div class="abs footer-divider"></div>
  <div class="abs footer-brand"><span class="brand-dot"></span>VELTRIX</div>
  <address class="abs address">
    27 Harbour Lane Level Two<br>2000 Sydney Australia<br>E-mail: info@veltrixmail.com<br>Phone: 02 9476 3318
  </address>
  <div class="abs bottom-bar"><span>Copyright © 2010 veltrix.com | All Rights Reserved</span><span>Call Us Now | Contact Us</span></div>
</footer>

</body>
</html>
```